KDWB Business Card

Looking for a business card design to incorporate our branding. We want to only use the colors listing in the Branding Package (attached).
Updates

Target Market(s)

People who need their phone or device fixed.

Industry/Entity Type

Electronics

Contact Information for Business Card

Please use:

Brightwick Gadget Clinic LLC
4810 E Harlow Ridge Rd
Suite 417
San Antonio, TX 78163

Marcus Delgrove, Store Manager

(210) 555-0147

Requirements
Must have
• Must include the colors that are contained within the Branding Package PDF file.

```html
<!DOCTYPE html>
<html lang="en">
<head>
<meta charset="utf-8">
<title>Brightwick Gadget Clinic – Business Card</title>
<link rel="stylesheet" href="https://fonts.googleapis.com/css2?family=Nunito+Sans:wght@400;600&display=swap">
<style>
  :root {
    --backdrop: #3a3430;
    --card: #1b1b1b;
    --orange: #f15a22;
    --text: #e8e8e8;
    --muted: #5a5a5a;
  }
  * { margin: 0; padding: 0; box-sizing: border-box; }
  html, body { width: 1200px; height: 764px; overflow: hidden; }
  body {
    background: var(--backdrop);
    font-family: "Nunito Sans", Arial, sans-serif;
    color: var(--text);
    position: relative;
  }
  .card {
    position: absolute;
    top: 227px;
    width: 540px;
    height: 310px;
    background: var(--card);
    border-radius: 4px;
    box-shadow: 0 14px 30px rgba(0,0,0,.45);
  }
  .card--front { left: 50px; }
  .card--back { left: 610px; display: flex; align-items: center; justify-content: center; }

  .brand { display: flex; align-items: center; gap: 12px; }
  .brand__mark {
    width: 34px; height: 34px;
    background: var(--orange);
    border-radius: 6px;
    flex: none;
  }
  .brand__name {
    font-weight: 400;
    font-size: 26px;
    color: var(--orange);
    letter-spacing: .2px;
    white-space: nowrap;
  }
  .card--front .brand { position: absolute; left: 122px; top: 52px; }

  .person {
    position: absolute;
    right: 292px;
    top: 164px;
    text-align: right;
  }
  .person__name { font-size: 21px; line-height: 1.1; }
  .person__role { font-size: 12px; color: var(--orange); margin-bottom: 18px; }
  .person__address { font-size: 13px; line-height: 1.35; }

  .divider {
    position: absolute;
    left: 270px; top: 146px;
    width: 2px; height: 124px;
    background: var(--text);
  }

  .contacts {
    position: absolute;
    left: 290px; top: 150px;
    list-style: none;
    font-size: 13px;
  }
  .contacts li { display: flex; align-items: center; gap: 8px; height: 20px; }
  .contacts li.gap { margin-top: 26px; }
  .contacts svg { width: 14px; height: 14px; flex: none; }
</style>
</head>
<body>
  <section class="card card--front">
    <div class="brand">
      <span class="brand__mark"></span>
      <span class="brand__name">Brightwick Gadget Clinic</span>
    </div>

    <div class="person">
      <p class="person__name">Marcus Delgrove</p>
      <p class="person__role">Store Manager</p>
      <p class="person__address">4810 E Harlow Ridge Rd<br>Suite 417<br>San Antonio, TX 78163</p>
    </div>

    <div class="divider"></div>

    <ul class="contacts">
      <li>
        <svg viewBox="0 0 14 14" aria-hidden="true"><rect width="14" height="14" rx="2" fill="#f15a22"/><path d="M4 3.5l1.6-.4 1 2.2-1 .7a5 5 0 0 0 2.4 2.4l.7-1 2.2 1-.4 1.6c-3.6.2-6.7-2.9-6.5-6.5z" fill="#1b1b1b"/></svg>
        (210) 555-0147
      </li>
      <li class="gap">
        <svg viewBox="0 0 14 14" aria-hidden="true"><rect width="14" height="14" rx="2" fill="#f15a22"/><rect x="3" y="4.5" width="8" height="5.5" fill="none" stroke="#1b1b1b" stroke-width="1.1"/><path d="M3 4.5l4 3 4-3" fill="none" stroke="#1b1b1b" stroke-width="1.1"/></svg>
        marcus@brightwickclinic.com
      </li>
      <li>
        <svg viewBox="0 0 14 14" aria-hidden="true"><rect width="14" height="14" rx="2" fill="#f15a22"/><circle cx="7" cy="7" r="3.8" fill="none" stroke="#1b1b1b" stroke-width="1.1"/><path d="M3.2 7h7.6M7 3.2c-2 2.4-2 5.2 0 7.6M7 3.2c2 2.4 2 5.2 0 7.6" fill="none" stroke="#1b1b1b" stroke-width=".9"/></svg>
        www.brightwickclinic.com
      </li>
    </ul>
  </section>

  <section class="card card--back">
    <div class="brand">
      <span class="brand__mark"></span>
      <span class="brand__name">Brightwick Gadget Clinic</span>
    </div>
  </section>
</body>
</html>
```